New Dental Office Needs an Attractive and user friendly Website Designed

I need a website for a new dental office. The Name is Harrowfield Dentistry. I would like a Modern design with a user friendly interface and usability.
I would like a landing page, a page that lists the services we offer: Cosmetic Dentistry, Implants, Dental Hygiene, Emergency Services, Restorations, Dentures
Target Market(s)
Mid to upper class
Industry/Entity Type
Dentistry
Coding
Number of Pages Required
1 page
Requirements
Must have
- Landing page that has a scheduling option, Procedures, operating hours, and contact us info
Nice to have
- Appealing design, Soft comforting colors. Easy to navigate page, Modern and professional.

```html
<!DOCTYPE html>
<html lang="en">
<head>
<meta charset="utf-8">
<title>Harrowfield Dentistry – Website Design</title>
<link rel="stylesheet" href="https://fonts.googleapis.com/css2?family=Playfair+Display:wght@500;600&family=Poppins:wght@400;500;600&display=swap">
<style>
:root{
  --blue:#0a6de6;
  --blue-deep:#0758c4;
  --ink:#0f1b2d;
  --muted:#6b7280;
  --line:#e6e9ef;
  --soft:#f6f7f9;
  --tint:#edf4fe;
  --footer-dark:#0b1a33;
  --star:#f5b50a;
  --white:#ffffff;
}
*{box-sizing:border-box;margin:0;padding:0}
html,body{width:1200px;height:1200px;overflow:hidden}
body{font-family:"Poppins",sans-serif;color:var(--ink)}
.board{position:absolute;left:0;top:0;width:1932px;height:1932px;transform:scale(0.621118);transform-origin:0 0;
  background:linear-gradient(135deg,#e2f6fd 0%,#bfe0fb 45%,#93c4fa 100%);overflow:hidden}
.page{position:absolute;width:668px;background:var(--white);overflow:hidden}
.page-home{left:267px;top:60px;height:1430px}
.page-about{left:981px;top:404px;height:1463px}
.abs{position:absolute}
.serif{font-family:"Playfair Display",serif;font-weight:500;letter-spacing:-0.3px}
.eyebrow{font-size:6px;font-weight:500;color:var(--blue)}
.center{text-align:center;left:0;right:0}
.lead{font-size:6.2px;line-height:10.5px;color:var(--muted)}
.btn{display:flex;align-items:center;justify-content:center;border-radius:12px;font-size:5.6px;font-weight:600;letter-spacing:.2px;text-transform:uppercase}
.btn-blue{background:var(--blue);color:var(--white)}
.btn-white{background:var(--white);color:var(--blue)}
svg{display:block;flex-shrink:0}

/* header */
.site-header{left:0;top:0;width:668px;height:34px;background:var(--white)}
.brand{left:80px;top:11px;font-size:9px;font-weight:600;color:var(--ink)}
.nav{left:240px;top:13px;display:flex;gap:16px;font-size:5.6px;font-weight:500}
.call-pill{left:496px;top:7px;width:93px;height:20px;border:1px solid var(--blue);border-radius:11px;display:flex;align-items:center;gap:5px;padding-left:7px}
.call-pill small{display:block;font-size:4.2px;color:var(--muted)}
.call-pill b{display:block;font-size:6px;color:var(--blue);font-weight:600}

/* hero */
.hero{left:0;top:34px;width:668px;height:314px;background:radial-gradient(circle at 25% 40%,#d8f4fb 0%,#b5e6f7 45%,#9edcf3 100%);overflow:hidden}
.hero-blob{left:320px;top:50px;width:470px;height:470px;border-radius:50%;background:var(--blue)}
.hero-photo{left:352px;top:0;width:316px;height:314px;border-radius:160px 0 0 0;
  background:linear-gradient(160deg,#c79a6a 0%,#e6c3a4 35%,#f1ddd0 60%,#fafafa 100%)}
.badge{left:79px;top:78px;height:11px;padding:0 6px;border-radius:6px;background:var(--white);display:flex;align-items:center;gap:4px;font-size:4.6px;font-weight:500}
.badge i{width:3.5px;height:3.5px;border-radius:50%;background:#22c55e}
.hero-title{left:79px;top:99px;width:260px;font-size:33px;line-height:32px}
.hero-text{left:79px;top:172px;width:250px;font-size:6.6px;line-height:11px;color:#3e4a5c}
.hero-btn{left:79px;top:218px;width:98px;height:19px}

/* info bar */
.info-bar{left:0;top:348px;width:668px;height:52px;background:var(--blue);color:var(--white)}
.info-item{top:16px;display:flex;align-items:center;gap:6px}
.info-item small{display:block;font-size:4.8px;opacity:.8}
.info-item b{display:block;font-size:6px;font-weight:500}
.info-btn{left:488px;top:16px;width:98px;height:20px}

/* section heading block */
.sec-eyebrow{top:48px}
.sec-title{top:60px}
.sec-lead{top:112px}

/* services */
.services{left:0;top:400px;width:668px;height:540px;background:var(--white)}
.section-title{font-size:20px;line-height:22px}
.service-grid{left:80px;top:157px;display:grid;grid-template-columns:repeat(3,164px);gap:9px 8px}
.service-card{height:136px;border:1px solid var(--line);border-radius:6px;padding:14px 15px;position:relative;background:var(--white)}
.service-card.is-active{background:var(--tint);border-color:#dbe8fb}
.service-card h3{position:absolute;top:52px;left:15px;font-size:7.4px;font-weight:500}
.service-card p{position:absolute;top:68px;left:15px;right:12px;font-size:5.6px;line-height:10px;color:var(--muted)}
.service-card .go{position:absolute;top:106px;left:15px}
.services-btn{left:278px;top:462px;width:111px;height:19px}

/* procedures */
.procedures{left:0;top:940px;width:668px;height:490px;background:var(--soft)}
.proc-photo{left:79px;top:157px;width:207px;height:188px;border-radius:6px;background:linear-gradient(140deg,#d9e4ec 0%,#6f8aa0 35%,#c8a48c 60%,#3c9bd3 100%)}
.accordion{left:310px;top:157px;width:279px;height:188px;background:var(--white);border-radius:6px;padding:0 11px;overflow:hidden}
.acc-row{display:flex;justify-content:space-between;align-items:center;font-size:7px;font-weight:600;height:25px;border-bottom:1px solid var(--line)}
.acc-open{height:110px;border-bottom:1px solid var(--line);padding-top:10px}
.acc-open .acc-head{display:flex;justify-content:space-between;align-items:center;font-size:7px;font-weight:600;height:20px;padding-bottom:8px;margin-bottom:7px;border-bottom:1px solid var(--line)}
.acc-item{display:flex;align-items:center;gap:4px;font-size:5.6px;color:var(--muted);height:14px}
.cta{left:79px;top:380px;width:510px;height:63px;background:var(--blue);border-radius:6px;color:var(--white)}
.cta h3{position:absolute;left:25px;top:15px;font-size:11px;font-weight:600}
.cta p{position:absolute;left:25px;top:32px;width:240px;font-size:5.6px;line-height:10px;opacity:.9}
.cta .btn{position:absolute;left:374px;top:22px;width:111px;height:19px}

/* why */
.why{left:0;top:0;width:668px;height:356px;background:var(--white)}
.why-title{left:79px;top:63px;width:240px;font-size:19px;line-height:22px}
.why-text{left:79px;top:115px;width:240px}
.feature{left:79px;width:243px;height:44px;border-radius:5px;background:var(--soft);display:flex;align-items:center;padding-left:12px;gap:12px}
.feature h4{font-size:6.8px;font-weight:500;margin-bottom:4px}
.feature p{font-size:5.2px;line-height:9px;color:var(--muted);width:180px}
.photo{border-radius:6px}

/* team */
.team{left:0;top:356px;width:668px;height:370px;background:var(--soft)}
.member{top:135px;width:121px}
.member .pic{width:121px;height:157px;border-radius:5px}
.member h4{font-size:6.4px;font-weight:500;text-align:center;margin-top:7px}
.member span{display:block;font-size:5px;color:var(--muted);text-align:center;margin-top:2px}

/* reviews */
.reviews{left:0;top:726px;width:668px;height:372px;background:var(--white)}
.review{top:147px;width:110px}
.review-head{display:flex;align-items:center;gap:4px;font-size:5.2px;font-weight:500}
.review-head .avatar{width:13px;height:13px;border-radius:50%}
.review-head .mark{margin-left:auto;width:6px;height:6px;border-radius:50%;background:#d6dbe3}
.review p{font-size:5.2px;line-height:9.2px;color:var(--muted);margin-top:9px;height:62px}
.stars{color:var(--star);font-size:7px;letter-spacing:2px;margin-top:2px}
.arrows{left:314px;top:299px;display:flex;gap:5px}

/* footer */
.footer{left:0;top:1098px;width:668px;height:338px;background:var(--blue);color:var(--white)}
.footer-brand{left:79px;top:42px;font-size:11px;font-weight:500}
.footer-text{left:79px;top:63px;width:180px;font-size:5.4px;line-height:10px;opacity:.85}
.rule{left:79px;width:184px;height:1px;background:rgba(255,255,255,.25)}
.contact{left:79px;display:flex;gap:8px;font-size:5.2px;line-height:9px}
.links-head{font-size:5px;letter-spacing:.5px;opacity:.7;text-transform:uppercase}
.links{font-size:5.2px;line-height:14.6px;margin-top:6px;list-style:none}
.form-card{left:311px;top:16px;width:278px;height:306px;background:var(--white);border-radius:5px;color:var(--ink);padding:18px 16px}
.form-card h3{font-size:10px;font-weight:600}
.form-card .intro{font-size:5.4px;line-height:10px;color:var(--muted);margin-top:4px;width:230px}
.fields{display:grid;grid-template-columns:117px 117px;gap:10px 12px;margin-top:12px}
.field label{display:block;font-size:5.4px;font-weight:500;margin-bottom:5px}
.input{height:19px;border:1px solid #cfd5de;border-radius:2px;font-size:5px;color:#9aa3b0;display:flex;align-items:center;justify-content:space-between;padding:0 6px}
.field-wide{grid-column:1 / 3}
.textarea{height:47px;align-items:flex-start;padding-top:7px}
.form-btn{margin-top:13px;width:95px;height:18px}
.bottom-bar{left:0;top:1436px;width:668px;height:27px;background:var(--footer-dark);color:rgba(255,255,255,.7);font-size:4.8px}
</style>
</head>
<body>
<div class="board">

  <!-- Home page -->
  <div class="page page-home">
    <header class="site-header abs">
      <div class="brand abs">Harrowfield Dentistry</div>
      <nav class="nav abs"><span>Home</span><span>About Us</span><span>Services</span><span>Procedures</span><span>Contact</span></nav>
      <div class="call-pill abs">
        <svg width="10" height="10" viewBox="0 0 24 24" fill="none" stroke="#0a6de6" stroke-width="2"><path d="M5 3h4l2 5-3 2a12 12 0 0 0 6 6l2-3 5 2v4a2 2 0 0 1-2 2A17 17 0 0 1 3 5a2 2 0 0 1 2-2z"/></svg>
        <div><small>Need Dental Services?</small><b>Call: +1 555 014 2270</b></div>
      </div>
    </header>

    <section class="hero abs">
      <div class="hero-blob abs"></div>
      <div class="hero-photo abs" role="img" aria-label="Smiling young woman with long wavy hair touching her chin"></div>
      <div class="badge abs"><i></i>Accepting New Patients</div>
      <h1 class="hero-title abs serif">Your Smile is Our Priority</h1>
      <p class="hero-text abs">Experience gentle, comprehensive dental care in a comfortable environment. We're dedicated to helping you achieve your healthiest, most beautiful smile.</p>
      <div class="hero-btn btn btn-blue abs">Book an Appointment</div>
    </section>

    <div class="info-bar abs">
      <div class="info-item abs" style="left:83px">
        <svg width="12" height="12" viewBox="0 0 24 24" fill="none" stroke="#fff" stroke-width="1.6"><path d="M5 3h4l2 5-3 2a12 12 0 0 0 6 6l2-3 5 2v4a2 2 0 0 1-2 2A17 17 0 0 1 3 5a2 2 0 0 1 2-2z"/></svg>
        <div><small>Need Dental Services?</small><b>+1 555 014 2270</b></div>
      </div>
      <div class="info-item abs" style="left:233px">
        <svg width="12" height="12" viewBox="0 0 24 24" fill="none" stroke="#fff" stroke-width="1.6"><circle cx="12" cy="12" r="10"/><path d="M12 6v6l4 2"/></svg>
        <div><small>Opening Hours</small><b>Mon to Sat 08:00 - 20:00</b></div>
      </div>
      <div class="info-btn btn btn-white abs">Book an Appointment</div>
    </div>

    <section class="services abs">
      <div class="eyebrow sec-eyebrow abs center">Our Services</div>
      <h2 class="section-title sec-title serif abs center">Comprehensive Dental<br>Services</h2>
      <p class="lead sec-lead abs center">From routine cleanings to complex procedures, we offer a full range of dental<br>services to keep your smile healthy and beautiful.</p>

      <div class="service-grid abs">
        <div class="service-card is-active">
          <svg width="26" height="26" viewBox="0 0 24 24" fill="none" stroke="#0a6de6" stroke-width="1"><path d="M7 3c-3 0-4 3-3 6 1 2 1 4 1.5 7 .4 3 1.5 5 2.5 5s1.5-3 2-5 1-2 2-2 1.5 0 2 2 1 5 2 5"/><path d="M18 3l.7 1.8L20.5 5.5 18.7 6.2 18 8l-.7-1.8-1.8-.7 1.8-.7z"/></svg>
          <h3>Cosmetic Dentistry</h3>
          <p>Transform your smile with veneers, whitening, and cosmetic bonding for a confident, beautiful appearance.</p>
          <svg class="go" width="12" height="12" viewBox="0 0 24 24" fill="none" stroke="#0a6de6" stroke-width="1.6"><circle cx="12" cy="12" r="10.5"/><path d="M9 15l6-6M10 9h5v5"/></svg>
        </div>
        <div class="service-card">
          <svg width="26" height="26" viewBox="0 0 24 24" fill="none" stroke="#0a6de6" stroke-width="1"><path d="M6 3c-2 0-3 2-2 5 .5 1.5 2 2 8 2s7.5-.5 8-2c1-3 0-5-2-5-2 0-3 1-6 1S8 3 6 3z"/><path d="M9 12h6M9.5 14.5h5M10 17h4M11 19.5h2"/></svg>
          <h3>Dental Implants</h3>
          <p>Replace missing teeth with dental implants that look, feel, and function just like your natural teeth.</p>
          <svg class="go" width="12" height="12" viewBox="0 0 24 24" fill="none" stroke="#0a6de6" stroke-width="1.6"><circle cx="12" cy="12" r="10.5"/><path d="M9 15l6-6M10 9h5v5"/></svg>
        </div>
        <div class="service-card">
          <svg width="26" height="26" viewBox="0 0 24 24" fill="none" stroke="#0a6de6" stroke-width="1"><path d="M5 5c-2 0-3 2-2 5 .5 2 1 4 1.5 7s1 4 2 4 1.2-3 1.7-5 1-2 1.8-2"/><circle cx="15" cy="8" r="4"/><path d="M18 11l4 5"/></svg>
          <h3>Dental Hygiene</h3>
          <p>Maintain your oral health with professional cleanings, exams, and personalized preventive care.</p>
          <svg class="go" width="12" height="12" viewBox="0 0 24 24" fill="none" stroke="#0a6de6" stroke-width="1.6"><circle cx="12" cy="12" r="10.5"/><path d="M9 15l6-6M10 9h5v5"/></svg>
        </div>
        <div class="service-card">
          <svg width="26" height="26" viewBox="0 0 24 24" fill="none" stroke="#0a6de6" stroke-width="1"><path d="M6 4c-3 0-4 3-3 6 1 2 1 4 1.5 7 .4 3 1.5 5 2.5 5s1.5-3 2-5 1-2 2-2"/><path d="M16 3l5 8h-10z"/><path d="M16 6v2.5M16 9.5v.3"/></svg>
          <h3>Emergency Services</h3>
          <p>Fast relief for dental emergencies including toothaches, broken teeth, and other urgent dental issues.</p>
          <svg class="go" width="12" height="12" viewBox="0 0 24 24" fill="none" stroke="#0a6de6" stroke-width="1.6"><circle cx="12" cy="12" r="10.5"/><path d="M9 15l6-6M10 9h5v5"/></svg>
        </div>
        <div class="service-card">
          <svg width="26" height="26" viewBox="0 0 24 24" fill="none" stroke="#0a6de6" stroke-width="1"><path d="M5 3v5l-1.5 3M5 8l1.5 3M5 11v10"/><circle cx="16" cy="6" r="3.5"/><path d="M16 9.5V21M13 13h6"/></svg>
          <h3>Restorations</h3>
          <p>Restore damaged teeth with fillings, crowns, bridges, and other treatments that bring back function and aesthetics.</p>
          <svg class="go" width="12" height="12" viewBox="0 0 24 24" fill="none" stroke="#0a6de6" stroke-width="1.6"><circle cx="12" cy="12" r="10.5"/><path d="M9 15l6-6M10 9h5v5"/></svg>
        </div>
        <div class="service-card">
          <svg width="26" height="22" viewBox="0 0 24 20" fill="none" stroke="#0a6de6" stroke-width="1"><rect x="2" y="3" width="20" height="6" rx="2"/><rect x="2" y="11" width="20" height="6" rx="2"/><path d="M6 3v6M10 3v6M14 3v6M18 3v6M6 11v6M10 11v6M14 11v6M18 11v6"/></svg>
          <h3 style="top:48px">Dentures</h3>
          <p style="top:64px">Custom-fitted full and partial dentures to replace missing teeth and restore your ability to eat and speak comfortably.</p>
          <svg class="go" style="top:102px" width="12" height="12" viewBox="0 0 24 24" fill="none" stroke="#0a6de6" stroke-width="1.6"><circle cx="12" cy="12" r="10.5"/><path d="M9 15l6-6M10 9h5v5"/></svg>
        </div>
      </div>
      <div class="services-btn btn btn-blue abs">Schedule a Consultation</div>
    </section>

    <section class="procedures abs">
      <div class="eyebrow sec-eyebrow abs center">Procedures</div>
      <h2 class="section-title sec-title serif abs center">Comprehensive Range of<br>Dental Procedures</h2>
      <p class="lead sec-lead abs center">We offer a comprehensive range of dental procedures using the latest<br>techniques and technologies for optimal results.</p>
      <div class="proc-photo abs" role="img" aria-label="Dentist in a mask adjusting the lamp beside a smiling patient in the chair"></div>
      <div class="accordion abs">
        <div class="acc-open">
          <div class="acc-head">Preventive
            <svg width="7" height="7" viewBox="0 0 24 24" fill="none" stroke="#0f1b2d" stroke-width="2.5"><path d="M6 15l6-6 6 6"/></svg></div>
          <div class="acc-item"><svg width="8" height="8" viewBox="0 0 24 24" fill="none" stroke="#0a6de6" stroke-width="2.4"><circle cx="12" cy="12" r="10"/><path d="M7.5 12.5l3 3 6-6"/></svg>Dental Cleaning</div>
          <div class="acc-item"><svg width="8" height="8" viewBox="0 0 24 24" fill="none" stroke="#0a6de6" stroke-width="2.4"><circle cx="12" cy="12" r="10"/><path d="M7.5 12.5l3 3 6-6"/></svg>Oral Examination</div>
          <div class="acc-item"><svg width="8" height="8" viewBox="0 0 24 24" fill="none" stroke="#0a6de6" stroke-width="2.4"><circle cx="12" cy="12" r="10"/><path d="M7.5 12.5l3 3 6-6"/></svg>Digital X-rays</div>
          <div class="acc-item"><svg width="8" height="8" viewBox="0 0 24 24" fill="none" stroke="#0a6de6" stroke-width="2.4"><circle cx="12" cy="12" r="10"/><path d="M7.5 12.5l3 3 6-6"/></svg>Fluoride Treatment</div>
          <div class="acc-item"><svg width="8" height="8" viewBox="0 0 24 24" fill="none" stroke="#0a6de6" stroke-width="2.4"><circle cx="12" cy="12" r="10"/><path d="M7.5 12.5l3 3 6-6"/></svg>Dental Sealants</div>
        </div>
        <div class="acc-row">Restorative<svg width="7" height="7" viewBox="0 0 24 24" fill="none" stroke="#0f1b2d" stroke-width="2.5"><path d="M6 9l6 6 6-6"/></svg></div>
        <div class="acc-row">Cosmetic<svg width="7" height="7" viewBox="0 0 24 24" fill="none" stroke="#0f1b2d" stroke-width="2.5"><path d="M6 9l6 6 6-6"/></svg></div>
        <div class="acc-row" style="border-bottom:0">Specialty<svg width="7" height="7" viewBox="0 0 24 24" fill="none" stroke="#0f1b2d" stroke-width="2.5"><path d="M6 9l6 6 6-6"/></svg></div>
      </div>
      <div class="cta abs">
        <h3>Not Sure What You Need?</h3>
        <p>Book a consultation with our dental team. We'll assess your oral health and recommend the most appropriate treatments for your specific needs.</p>
        <div class="btn btn-white">Schedule a Consultation</div>
      </div>
    </section>
  </div>

  <!-- About page -->
  <div class="page page-about">
    <section class="why abs">
      <div class="eyebrow abs" style="left:79px;top:50px">Why Choose Us</div>
      <h2 class="why-title serif abs">Why You Should Choose Harrowfield Dentistry ?</h2>
      <p class="why-text lead abs">We combine advanced technology with compassionate care to provide you with the best dental experience possible.</p>
      <div class="feature abs" style="top:148px">
        <svg width="16" height="16" viewBox="0 0 24 24" fill="none" stroke="#0f1b2d" stroke-width="1.2"><path d="M3 6l4 8h10l3 3M7 14l-2 6h14M12 4l3 5"/></svg>
        <div><h4>Modern Technology</h4><p>State-of-the-art equipment for precise and comfortable treatments.</p></div>
      </div>
      <div class="feature abs" style="top:204px;height:36px">
        <svg width="16" height="16" viewBox="0 0 24 24" fill="none" stroke="#0f1b2d" stroke-width="1.2"><circle cx="12" cy="7" r="4"/><path d="M4 21c0-4 3.5-7 8-7s8 3 8 7M9 14v3M15 14v3"/></svg>
        <div><h4>Experienced Team</h4><p>Our dentists have over 20 years of combined experience.</p></div>
      </div>
      <div class="feature abs" style="top:255px">
        <svg width="16" height="16" viewBox="0 0 24 24" fill="none" stroke="#0f1b2d" stroke-width="1.2"><rect x="5" y="4" width="14" height="17" rx="1"/><path d="M9 4V2h6v2M8 9h8M8 13h8M8 17h5"/></svg>
        <div><h4>Comprehensive Care</h4><p>All your dental needs addressed under one roof.</p></div>
      </div>
      <div class="photo abs" style="left:356px;top:45px;width:107px;height:122px;background:linear-gradient(160deg,#c9d3da,#7d5a48 55%,#2f3338)" role="img" aria-label="Smiling patient in the dental chair with a dentist nearby"></div>
      <div class="photo abs" style="left:346px;top:176px;width:117px;height:122px;background:linear-gradient(150deg,#e9d9b8,#dfe7ee 40%,#4b86c8 100%)" role="img" aria-label="Masked dentist examining a patient under the lamp"></div>
      <div class="photo abs" style="left:472px;top:95px;width:117px;height:153px;background:linear-gradient(160deg,#dde4e9,#c8a183 45%,#5f7fa3 100%)" role="img" aria-label="Nurse and senior patient giving a thumbs up"></div>
    </section>

    <section class="team abs">
      <div class="eyebrow abs center" style="top:48px">Our Team</div>
      <h2 class="section-title serif abs center" style="top:60px">Our Friendly Expert Team</h2>
      <p class="lead abs center" style="top:90px">Our experienced dental team is here to make every visit positive and personalized.<br>With gentle hands and caring hearts.</p>
      <div class="member abs" style="left:79px">
        <div class="pic" style="background:linear-gradient(170deg,#e3e8ec,#b9cde0 55%,#8aa9c8)" role="img" aria-label="Portrait of a senior dentist in light blue scrubs"></div>
        <h4>Dr. Martin Ellery</h4><span>Lead Dentist</span></div>
      <div class="member abs" style="left:209px">
        <div class="pic" style="background:linear-gradient(170deg,#d8dde2,#9a7a64 45%,#2f5fb0)" role="img" aria-label="Portrait of a dentist in blue scrubs beside a dental chair"></div>
        <h4>Dr. Nora Castell</h4><span>Senior Dentist</span></div>
      <div class="member abs" style="left:338px">
        <div class="pic" style="background:linear-gradient(170deg,#e5e7ea,#d6d9de 50%,#b8bfc8)" role="img" aria-label="Portrait of a grey-haired dentist in a white coat"></div>
        <h4>Dr. Peter Lindqvist</h4><span>Periodontist</span></div>
      <div class="member abs" style="left:468px">
        <div class="pic" style="background:linear-gradient(170deg,#e6eaee,#b38f75 40%,#1c8a9a)" role="img" aria-label="Portrait of a hygienist in teal scrubs with arms crossed"></div>
        <h4>Dr. Helen Marsh</h4><span>Dental Hygienist</span></div>
    </section>

    <section class="reviews abs">
      <div class="eyebrow abs center" style="top:48px">Testimonial</div>
      <h2 class="section-title serif abs center" style="top:60px">Read Our Reviews</h2>
      <p class="lead abs center" style="top:88px">Don't just take our word for it - hear from our satisfied patients<br>about their experiences.</p>
      <div class="review abs" style="left:2px">
        <div class="review-head"><span class="avatar" style="background:#8b6f5e" role="img" aria-label="Reviewer photo"></span>Tom H.<span class="mark"></span></div>
        <p>"The cosmetic work they did on my teeth has given me so much confidence. I can't stop smiling now!"</p>
        <div class="stars">★★★★★</div></div>
      <div class="review abs" style="left:141px">
        <div class="review-head"><span class="avatar" style="background:#6b4e3d" role="img" aria-label="Reviewer photo"></span>Jessica W.<span class="mark"></span></div>
        <p>"From the moment I walked in, I knew I was in good hands. The office is modern and comfortable, and the entire team is knowledgeable and friendly. Best dental practice in town!"</p>
        <div class="stars">★★★★★</div></div>
      <div class="review abs" style="left:280px">
        <div class="review-head"><span class="avatar" style="background:#4b4f57" role="img" aria-label="Reviewer photo"></span>Michael R.<span class="mark"></span></div>
        <p>"Finally found a dentist I can trust! The team is professional, caring, and the office environment is so relaxing."</p>
        <div class="stars">★★★★★</div></div>
      <div class="review abs" style="left:419px">
        <div class="review-head"><span class="avatar" style="background:#c79a72" role="img" aria-label="Reviewer photo"></span>Sarah M.<span class="mark"></span></div>
        <p>"The staff at Harrowfield Dentistry made me feel so comfortable. Dr. Ellery explained everything clearly and the results exceeded my expectations!"</p>
        <div class="stars">★★★★★</div></div>
      <div class="review abs" style="left:558px">
        <div class="review-head"><span class="avatar" style="background:#5a4a42" role="img" aria-label="Reviewer photo"></span>Henry K.<span class="mark"></span></div>
        <p>"I've been terrified of dentists my whole life, but Harrowfield Dentistry changed that. Their gentle approach and calming environment made all the difference"</p>
        <div class="stars">★★★★★</div></div>
      <div class="arrows abs">
        <svg width="11" height="11" viewBox="0 0 24 24" fill="none" stroke="#0a6de6" stroke-width="1.8"><circle cx="12" cy="12" r="10.5"/><path d="M16 12H8M11 8l-4 4 4 4"/></svg>
        <svg width="11" height="11" viewBox="0 0 24 24" fill="none" stroke="#0a6de6" stroke-width="1.8"><circle cx="12" cy="12" r="10.5"/><path d="M8 12h8M13 8l4 4-4 4"/></svg>
      </div>
    </section>

    <footer class="footer abs">
      <div class="footer-brand abs">Harrowfield Dentistry</div>
      <p class="footer-text abs">Providing exceptional dental care for the entire family in a comfortable, modern environment.</p>
      <div class="rule abs" style="top:94px"></div>
      <div class="contact abs" style="top:108px">
        <svg width="7" height="7" viewBox="0 0 24 24" fill="none" stroke="#fff" stroke-width="2"><path d="M12 22s7-7 7-12a7 7 0 0 0-14 0c0 5 7 12 7 12z"/><circle cx="12" cy="10" r="2.5"/></svg>
        <span>48 Linden Row, Suite 204<br>Harrowfield, CA 90417</span></div>
      <div class="contact abs" style="top:134px">
        <svg width="7" height="7" viewBox="0 0 24 24" fill="none" stroke="#fff" stroke-width="2"><path d="M5 3h4l2 5-3 2a12 12 0 0 0 6 6l2-3 5 2v4a2 2 0 0 1-2 2A17 17 0 0 1 3 5a2 2 0 0 1 2-2z"/></svg>
        <span>+1 555 014 2270</span></div>
      <div class="contact abs" style="top:150px">
        <svg width="7" height="7" viewBox="0 0 24 24" fill="none" stroke="#fff" stroke-width="2"><rect x="3" y="5" width="18" height="16" rx="2"/><path d="M3 10h18M8 3v4M16 3v4"/></svg>
        <span>Mon to Sat 08:00 - 20:00</span></div>
      <div class="contact abs" style="top:166px">
        <svg width="7" height="7" viewBox="0 0 24 24" fill="none" stroke="#fff" stroke-width="2"><rect x="3" y="5" width="18" height="14" rx="2"/><path d="M3 7l9 6 9-6"/></svg>
        <span>hello@harrowfielddental.com</span></div>
      <div class="rule abs" style="top:191px"></div>
      <div class="abs" style="left:79px;top:202px">
        <div class="links-head">Quick Links</div>
        <ul class="links"><li>Home</li><li>About Us</li><li>Services</li><li>Procedures</li><li>Testimonials</li><li>Contact</li></ul>
      </div>
      <div class="abs" style="left:187px;top:202px">
        <div class="links-head">Services</div>
        <ul class="links"><li>Cosmetic Dentistry</li><li>Dental Implants</li><li>Dental Hygiene</li><li>Emergency Services</li><li>Restorations</li><li>Dentures</li></ul>
      </div>

      <div class="form-card abs">
        <h3>Schedule Your Appointment</h3>
        <p class="intro">Book your visit online or call us directly. We look forward to welcoming you to our practice.</p>
        <div class="fields">
          <div class="field"><label>Full Name</label><div class="input">e.g. James Brown</div></div>
          <div class="field"><label>Email Address</label><div class="input">e.g. user@email.com</div></div>
          <div class="field"><label>Phone Number</label><div class="input">e.g. James Brown</div></div>
          <div class="field"><label>Service Needed</label><div class="input">Select a service
            <svg width="6" height="6" viewBox="0 0 24 24" fill="none" stroke="#0f1b2d" stroke-width="2.5"><path d="M6 9l6 6 6-6"/></svg></div></div>
          <div class="field"><label>Preferred Date</label><div class="input" style="color:#0f1b2d">Select a date
            <svg width="7" height="7" viewBox="0 0 24 24" fill="none" stroke="#0f1b2d" stroke-width="2"><rect x="3" y="5" width="18" height="16" rx="2"/><path d="M3 10h18M8 3v4M16 3v4"/></svg></div></div>
          <div class="field"><label>Preferred Time</label><div class="input" style="color:#0f1b2d">Select a time
            <svg width="7" height="7" viewBox="0 0 24 24" fill="none" stroke="#0f1b2d" stroke-width="2"><circle cx="12" cy="12" r="10"/><path d="M12 6v6l4 2"/></svg></div></div>
          <div class="field field-wide"><label>Additional Information</label><div class="input textarea">Please share any specific concerns or questions you have.</div></div>
        </div>
        <div class="form-btn btn btn-blue">Make an Appointment</div>
      </div>
    </footer>

    <div class="bottom-bar abs">
      <span class="abs" style="left:79px;top:11px">Copyright 2025 - Harrowfield Dentistry</span>
      <span class="abs" style="left:481px;top:11px">Terms &amp; Conditions</span>
      <span class="abs" style="left:547px;top:11px">Privacy Policy</span>
    </div>
  </div>

</div>
</body>
</html>
```